1/2 page ad, 1/2 HORIZONTAL 9.875" x 5", for magazine

We need an ad design that tastefully describes the services we offer.

The Meadowlark Heritage Centre is the heart of Vancouver. We provide classic, updated banquet halls with integrated audio visual capabilities and soaring ceilings. With nine rental halls we are home for international conferences, intimate family gatherings and celebrations for up to 1400 people. Our central location, free parking and full service catering are an ideal solution for weddings, celebrations of life and Christmas parties. With break out rooms and separate rooms for dining and meeting, we are a tremendous asset for the Vancouver destination conferences, awards nights and ceremonies.

1. A PDF x/1a file (CMYK, all fonts embedded, images 200ppi) Black or grey recommended
% of black only.
2. An Illustrator CS6 (or lower) file or eps file with all fonts converted to outlines and all
images embedded. Colour space must be CMYK, not RGB. Images should be 200ppi

```html
<!DOCTYPE html>
<html lang="en">
<head>
<meta charset="utf-8">
<title>The Heart of Vancouver – Ad Layouts</title>
<link rel="stylesheet" href="https://fonts.googleapis.com/css2?family=Poppins:wght@400;500;600;700;800;900&family=Oswald:wght@700&display=swap">
<style>
:root{
  --board:#4c505c;
  --paper:#ffffff;
  --red:#e53a2f;
  --red-deep:#c92b22;
  --blue:#2f4fa2;
  --ink:#1b1b1b;
  --bar:#1d1d1d;
  --photo:linear-gradient(180deg,#efe7d9 0%,#e6d7bd 30%,#f7f3ec 52%,#e3ad82 72%,#c9703f 100%);
}
*{box-sizing:border-box;margin:0;padding:0}
html,body{width:1200px;height:2400px;overflow:hidden;background:var(--board)}
body{position:relative;font-family:"Poppins",sans-serif;color:var(--ink)}

.ad{position:absolute;background:var(--paper);overflow:hidden;box-shadow:0 4px 14px rgba(0,0,0,.35)}
.ad *{position:absolute}
.ad--wide{left:176px;top:111px;width:849px;height:429px}
.ad--tall{left:176px;top:624px;width:849px;height:548px}
.ad--square{left:229px;top:1256px;width:743px;height:1053px}

.venue-photo{border-radius:50%;background:var(--photo);border:6px solid var(--blue);
  box-shadow:0 0 0 8px var(--paper),0 0 0 34px var(--red)}

.emblem{border-radius:50%;border:3px solid var(--blue);background:var(--paper);
  display:flex;align-items:center;justify-content:center;text-align:center}
.emblem span{position:static;font-weight:700;color:var(--blue);line-height:1.15}

.headline-top{font-weight:800;color:var(--ink);line-height:1;letter-spacing:-.5px;white-space:nowrap}
.headline-main{font-weight:900;color:var(--red);line-height:1;letter-spacing:-.5px;white-space:nowrap}

.capacity-ribbon{background:var(--red);transform:skewX(-18deg)}
.capacity-label{color:#fff;font-weight:600;white-space:nowrap;line-height:1}
.capacity-figure{font-family:"Oswald",sans-serif;font-weight:700;color:var(--blue);font-style:italic;
  transform:skewX(-10deg);line-height:1;white-space:nowrap;letter-spacing:-.5px}

.feature-band{background:var(--blue);display:flex}
.feature{position:relative !important;flex:1;display:flex;flex-direction:column;align-items:center;
  text-align:center;color:#fff;border-right:1.5px dashed rgba(255,255,255,.75)}
.feature:last-child{border-right:none}
.feature *{position:static}
.feature svg{border-radius:50%;background:#fff;border:2px solid var(--red)}
.feature p{line-height:1.2}

.intro{font-weight:400;white-space:nowrap}
.occasions{display:grid;grid-auto-flow:column;grid-template-rows:1fr 1fr}
.occasions li{position:relative;list-style:none;font-weight:600;display:flex;align-items:center;white-space:nowrap}
.occasions li svg{position:static;flex:none;margin-right:5px}

.contact-bar{background:var(--bar);border-radius:40px;color:#fff;display:flex;align-items:center;font-weight:600;white-space:nowrap;line-height:1}
.contact-bar *{position:static}
.contact-bar > *{flex:none}
.contact-bar .call{margin-right:18px}
.contact-bar .phone,.contact-bar .web{display:flex;align-items:center;gap:7px}
.contact-bar .divider{width:1.5px;align-self:stretch;background:#fff}
.contact-bar .web{font-weight:400}
.contact-bar .web b{color:var(--red);font-weight:600}
</style>
</head>
<body>

<svg width="0" height="0" style="position:absolute">
  <defs>
    <symbol id="icon-banquet" viewBox="0 0 40 40"><g fill="none" stroke="#2f4fa2" stroke-width="1.6"><path d="M12 17h16M14 17v-3a6 6 0 0 1 12 0v3M20 8v-2M10 21h20M13 21v9M27 21v9M17 21v6h6v-6"/></g></symbol>
    <symbol id="icon-people" viewBox="0 0 40 40"><g fill="none" stroke="#2f4fa2" stroke-width="1.6"><circle cx="14" cy="14" r="3.5"/><circle cx="26" cy="14" r="3.5"/><circle cx="20" cy="20" r="3.5"/><path d="M8 26a6 6 0 0 1 12 0M20 26a6 6 0 0 1 12 0M13 32a7 7 0 0 1 14 0"/></g></symbol>
    <symbol id="icon-rooms" viewBox="0 0 40 40"><g fill="none" stroke="#2f4fa2" stroke-width="1.6"><path d="M8 30V18h24v12M8 30h24M20 18v-6M16 12h8M12 30v-7h5v7M23 30v-7h5v7"/></g></symbol>
    <symbol id="icon-check" viewBox="0 0 14 14"><circle cx="7" cy="7" r="6" fill="none" stroke="#2f4fa2" stroke-width="1.2"/><path d="M4 7.2l2 2 4-4.4" fill="none" stroke="#e53a2f" stroke-width="1.5"/></symbol>
    <symbol id="icon-phone" viewBox="0 0 20 20"><circle cx="10" cy="10" r="10" fill="#2f4fa2"/><path d="M7 5l2 2.5-1.2 1.5a7 7 0 0 0 3.2 3.2l1.5-1.2L15 13l-1.2 1.8C9 14.5 5.5 11 5.2 6.2z" fill="#fff"/></symbol>
    <symbol id="icon-globe" viewBox="0 0 20 20"><g fill="none" stroke="#2f4fa2" stroke-width="1.6"><circle cx="10" cy="10" r="8.5"/><ellipse cx="10" cy="10" rx="4" ry="8.5"/><path d="M1.5 10h17M3 5.5h14M3 14.5h14"/></g></symbol>
  </defs>
</svg>

<!-- Layout 1: wide half-page -->
<section class="ad ad--wide">
  <div class="venue-photo" role="img" aria-label="Banquet hall set with round white tables, gold chairs and draped backdrop" style="left:523px;top:18px;width:398px;height:398px"></div>
  <div class="emblem" style="left:24px;top:22px;width:102px;height:102px"><span style="font-size:11px">Meadowlark<br>Heritage<br>Centre</span></div>
  <h1 class="headline-top" style="left:148px;top:38px;font-size:37px">THE HEART OF</h1>
  <h2 class="headline-main" style="left:148px;top:72px;font-size:53px">VANCOUVER</h2>
  <div class="capacity-ribbon" style="left:30px;top:139px;width:258px;height:27px"></div>
  <p class="capacity-label" style="left:42px;top:143px;font-size:20px">Celebrations for up to</p>
  <p class="capacity-figure" style="left:282px;top:128px;font-size:40px">1400 PEOPLE</p>
  <div class="feature-band" style="left:0;top:180px;width:495px;height:118px;padding:10px 0 8px">
    <div class="feature"><svg width="38" height="38"><use href="#icon-banquet"/></svg><p style="font-size:8.5px;margin-top:12px;padding:0 20px">We provide classic, updated banquet halls with integrated audio visual capabilities and soaring ceilings.</p></div>
    <div class="feature"><svg width="38" height="38"><use href="#icon-people"/></svg><p style="font-size:8.5px;margin-top:12px;padding:0 12px">With nine rental halls we are home for international conferences, intimate family gatherings.</p></div>
    <div class="feature"><svg width="38" height="38"><use href="#icon-rooms"/></svg><p style="font-size:8.5px;margin-top:12px;padding:0 14px">With break out rooms and separate rooms for dining and meeting, we are a tremendous asset for the Vancouver destination.</p></div>
  </div>
  <p class="intro" style="left:22px;top:307px;font-size:11.5px">Our central location, free parking and full service catering are an ideal solution for</p>
  <ul class="occasions" style="left:20px;top:329px;width:500px;height:44px;grid-template-columns:180px 170px 150px;font-size:13px">
    <li><svg width="11" height="11"><use href="#icon-check"/></svg>Weddings</li>
    <li><svg width="11" height="11"><use href="#icon-check"/></svg>Celebrations of life</li>
    <li><svg width="11" height="11"><use href="#icon-check"/></svg>Christmas parties</li>
    <li><svg width="11" height="11"><use href="#icon-check"/></svg>Conference</li>
    <li><svg width="11" height="11"><use href="#icon-check"/></svg>Awards nights</li>
    <li><svg width="11" height="11"><use href="#icon-check"/></svg>Ceremonies</li>
  </ul>
  <div class="contact-bar" style="left:18px;top:381px;width:626px;height:34px;padding-left:16px;font-size:17px">
    <span class="call">Call Us Now!</span>
    <span class="phone"><svg width="17" height="17"><use href="#icon-phone"/></svg>604-555-0188</span>
    <span class="web" style="margin-left:24px;font-size:17px"><svg width="19" height="19"><use href="#icon-globe"/></svg><span>www.<b>meadowlarkcentre</b>.com</span></span>
  </div>
</section>

<!-- Layout 2: taller half-page -->
<section class="ad ad--tall">
  <div class="venue-photo" role="img" aria-label="Banquet hall set with round white tables, gold chairs and draped backdrop" style="left:500px;top:46px;width:424px;height:424px"></div>
  <div class="emblem" style="left:14px;top:18px;width:108px;height:108px"><span style="font-size:12px">Meadowlark<br>Heritage<br>Centre</span></div>
  <h1 class="headline-top" style="left:139px;top:38px;font-size:39px">THE HEART OF</h1>
  <h2 class="headline-main" style="left:139px;top:72px;font-size:56px">VANCOUVER</h2>
  <div class="capacity-ribbon" style="left:18px;top:161px;width:262px;height:27px"></div>
  <p class="capacity-label" style="left:30px;top:165px;font-size:20px">Celebrations for up to</p>
  <p class="capacity-figure" style="left:270px;top:148px;font-size:42px">1400 PEOPLE</p>
  <div class="feature-band" style="left:0;top:214px;width:466px;height:172px;padding:14px 0 8px">
    <div class="feature"><svg width="42" height="42"><use href="#icon-banquet"/></svg><p style="font-size:12px;margin-top:12px;padding:0 22px">We provide classic, updated banquet halls with integrated audio visual capabilities and soaring ceilings.</p></div>
    <div class="feature"><svg width="42" height="42"><use href="#icon-people"/></svg><p style="font-size:12px;margin-top:12px;padding:0 14px">With nine rental halls we are home for international conferences, intimate family gatherings.</p></div>
    <div class="feature"><svg width="42" height="42"><use href="#icon-rooms"/></svg><p style="font-size:12px;margin-top:12px;padding:0 12px">With break out rooms and separate rooms for dining and meeting, we are a tremendous asset for the Vancouver destination.</p></div>
  </div>
  <p class="intro" style="left:27px;top:404px;font-size:11.5px">Our central location, free parking and full service catering are an ideal solution for</p>
  <ul class="occasions" style="left:26px;top:426px;width:500px;height:44px;grid-template-columns:178px 169px 150px;font-size:13px">
    <li><svg width="11" height="11"><use href="#icon-check"/></svg>Weddings</li>
    <li><svg width="11" height="11"><use href="#icon-check"/></svg>Celebrations of life</li>
    <li><svg width="11" height="11"><use href="#icon-check"/></svg>Christmas parties</li>
    <li><svg width="11" height="11"><use href="#icon-check"/></svg>Conference</li>
    <li><svg width="11" height="11"><use href="#icon-check"/></svg>Awards nights</li>
    <li><svg width="11" height="11"><use href="#icon-check"/></svg>Ceremonies</li>
  </ul>
  <div class="contact-bar" style="left:9px;top:489px;width:820px;height:37px;padding-left:19px;font-size:22px">
    <span class="call" style="margin-right:20px">Call Us Now!</span>
    <span class="phone"><svg width="21" height="21"><use href="#icon-phone"/></svg>604-555-0188</span>
    <span class="divider" style="margin-left:44px"></span>
    <span class="web" style="margin-left:52px;font-size:22px"><svg width="24" height="24"><use href="#icon-globe"/></svg><span>www.<b>meadowlarkcentre</b>.com</span></span>
  </div>
</section>

<!-- Layout 3: square portrait -->
<section class="ad ad--square">
  <div class="venue-photo" role="img" aria-label="Banquet hall set with round white tables, gold chairs and draped backdrop" style="left:55px;top:-276px;width:634px;height:634px"></div>
  <div class="emblem" style="left:288px;top:300px;width:168px;height:168px;border-width:4px"><span style="font-size:18px">Meadowlark<br>Heritage<br>Centre</span></div>
  <h1 class="headline-top" style="left:0;width:743px;text-align:center;top:487px;font-size:70px">THE HEART OF</h1>
  <h2 class="headline-main" style="left:0;width:743px;text-align:center;top:552px;font-size:94px">VANCOUVER</h2>
  <div class="capacity-ribbon" style="left:46px;top:656px;width:374px;height:38px"></div>
  <p class="capacity-label" style="left:66px;top:661px;font-size:29px">Celebrations for up to</p>
  <p class="capacity-figure" style="left:412px;top:636px;font-size:58px">1400 PEOPLE</p>
  <div class="feature-band" style="left:0;top:707px;width:743px;height:171px;padding:14px 0 8px">
    <div class="feature"><svg width="50" height="50"><use href="#icon-banquet"/></svg><p style="font-size:13px;margin-top:10px;padding:0 30px">We provide classic, updated banquet halls with integrated audio visual capabilities and soaring ceilings.</p></div>
    <div class="feature"><svg width="50" height="50"><use href="#icon-people"/></svg><p style="font-size:13px;margin-top:10px;padding:0 22px">With nine rental halls we are home for international conferences, intimate family gatherings.</p></div>
    <div class="feature"><svg width="50" height="50"><use href="#icon-rooms"/></svg><p style="font-size:13px;margin-top:10px;padding:0 22px">With break out rooms and separate rooms for dining and meeting, we are a tremendous asset for the Vancouver destination.</p></div>
  </div>
  <p class="intro" style="left:38px;top:890px;font-size:16.5px">Our central location, free parking and full service catering are an ideal solution for</p>
  <ul class="occasions" style="left:36px;top:918px;width:690px;height:62px;grid-template-columns:259px 247px 180px;font-size:19.5px">
    <li><svg width="16" height="16"><use href="#icon-check"/></svg>Weddings</li>
    <li><svg width="16" height="16"><use href="#icon-check"/></svg>Celebrations of life</li>
    <li><svg width="16" height="16"><use href="#icon-check"/></svg>Christmas parties</li>
    <li><svg width="16" height="16"><use href="#icon-check"/></svg>Conference</li>
    <li><svg width="16" height="16"><use href="#icon-check"/></svg>Awards nights</li>
    <li><svg width="16" height="16"><use href="#icon-check"/></svg>Ceremonies</li>
  </ul>
  <div class="contact-bar" style="left:21px;top:991px;width:693px;height:33px;padding-left:16px;font-size:18px">
    <span class="call">Call Us Now!</span>
    <span class="phone"><svg width="17" height="17"><use href="#icon-phone"/></svg>604-555-0188</span>
    <span class="divider" style="margin-left:36px"></span>
    <span class="web" style="margin-left:44px;font-size:18px"><svg width="19" height="19"><use href="#icon-globe"/></svg><span>www.<b>meadowlarkcentre</b>.com</span></span>
  </div>
</section>

</body>
</html>
```